Personal Chef Needs a Good Web Design

Hi everyone!
My name is Leo, I work as a private chef for last 10 years, traveling all around the world and cooking in private megayacht and villas.
I'm about to settle down in my hometown in Europe for a while. And therefore I need a website that will show my story, pics and recipes, nutritional advices and of course offer a Personal and Private Chef services( working for 4-5 families and bringing delicious food to their house).
My clients are extremely rich folks, but usually are down to earth ones.
I believe, the web site should be focused on attention to:
-VIP person's wife( as she is usually responsible for food for family) and be simple.
-to famous people agents and be on high level.

There will be about 10 different menus and 6 different service offers

--UPDATE--
Logo Design:
+My thoughts are- printed structure of the vegetable or fruit on a white font. Like you slice the buffalo tomato, put it in red paint and print it on the edge of the page. See attached files named logo. Can be any nice structured thing, like tomato, lemon, red cabbage etc.
+Classic logos with chef's hat or knives are good too.
+Need to have the space for me to add the name( the fonts can be provided)

Target Market(s)

Private person. 80% Russian clients.

Industry/Entity Type

Cooking

Coding

Coded - Design and coding required

Number of Pages Required

3 page

Requirements
Must have
• Contact form/ Request back call/ Schedule a free consultation
Nice to have
• The client will need to choose straight ahead from the range of services I offer, like:
• -Private Chef( cooking only for the client)
• -Personal Chef( cooking for around 5 clients, bringing the ready to be heated food to their door)
• -Romantic dinner for two
• -Professional Sommelier service
• -Build your kitchen( offering design, equipment and that will fit your requirements)
• -Other( flowers, waiters, barista, equipment rental)
• So this column should go right after the introduction/aboutme part and will lead to separate pages with how-it-works thing for each.

```html
<!DOCTYPE html>
<html lang="en">
<head>
<meta charset="utf-8">
<title>Leo Chef — Private &amp; Personal Chef</title>
<link href="https://fonts.googleapis.com/css2?family=Open+Sans:ital,wght@0,300;0,400;0,600;0,700;0,800;1,400&display=swap" rel="stylesheet">
<style>
:root{
  --green:#5aae0f;
  --ink:#3d3129;
  --text:#6a6a6a;
  --band:#f2f2f2;
  --white:#ffffff;
  --footer:#161616;
  --line:#c9c9c9;
  --brand:#3c3c3c;
}
*{box-sizing:border-box;margin:0;padding:0}
html,body{width:1200px;height:3358px;overflow:hidden}
body{position:relative;font-family:"Open Sans",Arial,sans-serif;background:var(--white);color:var(--text)}
.abs{position:absolute}

/* Top navigation */
.site-nav{position:absolute;left:0;top:0;width:1200px;height:94px;background:var(--white);z-index:5;box-shadow:0 2px 6px rgba(0,0,0,.12)}
.nav-links{position:absolute;top:38px;display:flex;font-size:14px;font-weight:600;text-transform:uppercase;color:#3a3a3a;letter-spacing:.2px}
.nav-links a{color:inherit;text-decoration:none;margin-right:50px}
.nav-links a.is-active{color:var(--green)}
.nav-left{left:74px}
.nav-right{left:760px}
.nav-badge{position:absolute;left:510px;top:0;z-index:6;width:180px;height:130px}
.brand{position:absolute;left:0;top:30px;width:180px;text-align:center;font-weight:800;color:var(--brand);font-size:30px;line-height:36px;white-space:nowrap}

/* Hero */
.hero{position:absolute;left:0;top:94px;width:1200px;height:562px;background:linear-gradient(180deg,#6d7376 0%,#8e9394 35%,#5f6a6b 60%,#7a4a35 80%,#5a3a2a 100%)}
.hero-title{position:absolute;left:112px;top:262px;font-size:70px;font-weight:800;color:var(--green);line-height:1;letter-spacing:1px}
.hero-lead{position:absolute;left:116px;top:346px;width:520px;font-size:19px;font-weight:600;color:var(--white);line-height:29px}
.hero-arrow{position:absolute;top:326px}

/* Shared */
.section-title{font-size:32px;font-weight:400;color:var(--ink);text-transform:uppercase;letter-spacing:.5px;line-height:1}
.body-text{font-size:15px;line-height:28px;color:var(--text)}
.btn-outline{position:absolute;display:flex;align-items:center;justify-content:center;border:1px solid var(--line);color:var(--green);font-size:17px;text-transform:uppercase;background:transparent}

/* Welcome */
.welcome-photo{position:absolute;left:84px;top:683px;width:384px;height:526px;border-radius:0 0 120px 0;background:radial-gradient(ellipse at 50% 40%,#f4f4f4 0%,#e6e6e6 60%,#d7d9dc 100%)}

/* Story */
.story-frame{position:absolute;left:712px;top:1136px;width:488px;height:360px;overflow:hidden}
.story-photo{position:absolute;left:0;top:-200px;width:560px;height:560px;border-radius:50%;background:radial-gradient(circle at 45% 60%,#c9b49a 0%,#8a7563 45%,#3e3630 100%)}

/* Services */
.service{position:absolute;top:1692px;width:360px;text-align:center}
.service-icon{width:108px;height:108px;margin:0 auto;border:3px solid #4a3a2e;border-radius:50%;display:flex;align-items:center;justify-content:center}
.service-icon span{display:block;width:56px;height:56px;border-radius:50%;background:linear-gradient(#6fbf22,#3f3a33)}
.service h3{margin-top:30px;font-size:24px;font-weight:400;color:var(--green);text-transform:uppercase;line-height:1}
.service p{width:310px;margin:12px auto 0;font-size:15px;line-height:22px;color:var(--text)}

/* How it works */
.steps{position:absolute;top:2138px;width:520px;list-style:none}
.steps li{position:relative;padding-left:34px;font-size:14px;line-height:23px;color:var(--text);margin-bottom:20px}
.steps svg{position:absolute;left:0;top:5px}

/* Recipes */
.recipes{position:absolute;left:0;top:2362px;width:1200px;height:522px;background:linear-gradient(135deg,#2a1f1a 0%,#1b1614 50%,#2b201b 100%)}
.recipe-card{position:absolute;top:2528px;width:251px;height:197px}
.btn-light{position:absolute;top:2776px;height:54px;display:flex;align-items:center;justify-content:center;border:1px solid #8a8a8a;color:var(--green);font-size:17px;text-transform:uppercase}

/* Testimonials & signup */
.quote-text{position:absolute;left:257px;top:2968px;width:500px;font-size:15px;font-style:italic;line-height:28px;color:var(--text)}
.email-field{position:absolute;left:795px;top:3031px;width:331px;height:44px;border:1px solid #d6d6d6;background:#f7f7f7;font-size:14px;color:#999;padding:12px 14px}

/* Footer */
.footer-nav{position:absolute;top:3218px;right:74px;display:flex;gap:30px;font-size:12px;font-weight:600;color:var(--white);text-transform:uppercase}
.footer-brand{position:absolute;left:78px;top:3276px;font-weight:800;color:#6e6e6e;font-size:22px;line-height:28px;white-space:nowrap}
.footer-copy{position:absolute;left:186px;top:3272px;font-size:11px;color:#777;line-height:20px}
.social{position:absolute;top:3277px;left:922px;display:flex;gap:14px}
.social span{width:22px;height:22px;border-radius:3px;background:var(--green)}
</style>
</head>
<body>

<!-- Navigation -->
<header class="site-nav">
  <nav class="nav-links nav-left">
    <a class="is-active">Home</a><a>About Chef</a><a>Menu</a><a>Recipes</a>
  </nav>
  <nav class="nav-links nav-right">
    <a>How It Works</a><a>Services</a><a>Get In Touch</a>
  </nav>
</header>
<div class="nav-badge">
  <svg width="180" height="130" viewBox="0 0 180 130"><polygon points="0,0 180,0 180,94 90,128 0,94" fill="#fff"/></svg>
  <div class="brand">Leo Chef</div>
</div>

<!-- Hero -->
<section class="hero" role="img" aria-label="Smiling chef by the sea holding a platter of seafood with lemons and lobster"></section>
<h1 class="hero-title">LEO CHEF</h1>
<p class="hero-lead">I work as a private chef for last 10 years, traveling all around the world and cooking in private megayacht and villas.</p>
<svg class="hero-arrow" style="left:46px" width="28" height="48" viewBox="0 0 28 48"><polyline points="24,4 4,24 24,44" fill="none" stroke="#fff" stroke-width="4" opacity=".85"/></svg>
<svg class="hero-arrow" style="left:1112px" width="28" height="48" viewBox="0 0 28 48"><polyline points="4,4 24,24 4,44" fill="none" stroke="#fff" stroke-width="4" opacity=".85"/></svg>

<!-- Story band background -->
<svg class="abs" style="left:0;top:1120px" width="1200" height="480" viewBox="0 0 1200 480">
  <polygon points="0,40 1200,16 1200,470 0,390" fill="#f2f2f2"/>
</svg>

<!-- Welcome -->
<div class="welcome-photo" role="img" aria-label="Chef in white jacket and tall hat with arms crossed"></div>
<h2 class="section-title abs" style="left:524px;top:734px">Welcome to my website</h2>
<p class="body-text abs" style="left:524px;top:790px;width:600px">Aliquam molestie, mi et imperdiet euismod, dui purus auctor tellus, et interdum lacus lectus et ante. Sed accumsan sollicitudin sapien, sit amet adipiscing turpis gravida ac. In congue, neque ac lobortis volutpat, libero mauris varius mi, vitae suscipit ipsum ligula vitae risus. Duis aliquam nibh a dui iaculis viverra id a velit. Vivamus egestas risus in magna varius commodo. Sed semper viverra egestas. Etiam pretium porttitor lectus, vel ornare neque porta volutpat.</p>
<div class="btn-outline" style="left:524px;top:1003px;width:166px;height:56px">Read More</div>

<!-- My story -->
<div class="story-frame"><div class="story-photo" role="img" aria-label="Chef carefully plating a gourmet dish"></div></div>
<h2 class="section-title abs" style="left:72px;top:1258px">My Story</h2>
<p class="body-text abs" style="left:72px;top:1310px;width:610px">Aliquam molestie, mi et imperdiet euismod, dui purus auctor tellus, et interdum lacus lectus et ante. Sed accumsan sollicitudin sapien, sit amet adipiscing turpis gravida ac. In congue, neque ac lobortis volutpat, libero mauris varius mi..</p>
<div class="btn-outline" style="left:74px;top:1420px;width:166px;height:58px">Read More</div>

<!-- Services -->
<h2 class="section-title abs" style="left:0;top:1624px;width:1200px;text-align:center">My Services</h2>
<div class="service" style="left:60px">
  <div class="service-icon"><span role="img" aria-label="Scale with wheat and apple icon"></span></div>
  <h3>Nutritional Advices</h3>
  <p>Aliquam molestie, mi et imperdiet euismod, dui purus auctor tellus, et interdum lacus lectus et ante.</p>
</div>
<div class="service" style="left:420px">
  <div class="service-icon"><span role="img" aria-label="Chef figure icon"></span></div>
  <h3>Personal Chef Services</h3>
  <p>Aliquam molestie, mi et imperdiet euismod, dui purus auctor tellus, et interdum lacus lectus et ante.</p>
</div>
<div class="service" style="left:778px">
  <div class="service-icon"><span role="img" aria-label="Chef at a counter icon"></span></div>
  <h3>Private Chef Services</h3>
  <p>Aliquam molestie, mi et imperdiet euismod, dui purus auctor tellus, et interdum lacus lectus et ante.</p>
</div>

<!-- How it works band -->
<svg class="abs" style="left:0;top:1978px" width="1200" height="432" viewBox="0 0 1200 432">
  <polygon points="0,3 720,3 960,72 1200,3 1200,432 0,432" fill="#f2f2f2"/>
</svg>
<h2 class="section-title abs" style="left:0;top:2080px;width:1200px;text-align:center">How It Works</h2>
<ul class="steps" style="left:78px">
  <li><svg width="14" height="12" viewBox="0 0 14 12"><polyline points="1,6 5,10 13,1" fill="none" stroke="#5aae0f" stroke-width="2.5"/></svg>Our first consultation will be in your home. We will discuss any food preferences you may have, as well as any allergy or dietary needs.</li>
  <li><svg width="14" height="12" viewBox="0 0 14 12"><polyline points="1,6 5,10 13,1" fill="none" stroke="#5aae0f" stroke-width="2.5"/></svg>At this time we will also discus what kind of meals you like, from meat and potatoes to all organic, vegan and vegetarian meals or international cuisine like Italian or Mexican .</li>
  <li><svg width="14" height="12" viewBox="0 0 14 12"><polyline points="1,6 5,10 13,1" fill="none" stroke="#5aae0f" stroke-width="2.5"/></svg>If you have concerns about your diet we can work with any restrictions you have.</li>
</ul>
<ul class="steps" style="left:614px">
  <li><svg width="14" height="12" viewBox="0 0 14 12"><polyline points="1,6 5,10 13,1" fill="none" stroke="#5aae0f" stroke-width="2.5"/></svg>On your scheduled cook date &nbsp;We will prepare your meals in our commercial kitchen and drop them off to you at your convenience.</li>
  <li><svg width="14" height="12" viewBox="0 0 14 12"><polyline points="1,6 5,10 13,1" fill="none" stroke="#5aae0f" stroke-width="2.5"/></svg>Your meals will be chilled, packaged, labeled and stored in your refrigerator or freezer with easy instructions for heating.</li>
  <li><svg width="14" height="12" viewBox="0 0 14 12"><polyline points="1,6 5,10 13,1" fill="none" stroke="#5aae0f" stroke-width="2.5"/></svg>Meals can be packaged in single servings or family style. All meals will have special heating instructions which most only require you heating it up in the oven.</li>
</ul>

<!-- Recipes -->
<section class="recipes" role="img" aria-label="Dark kitchen table with a recipe book in the background"></section>
<svg class="abs" style="left:0;top:2360px" width="1200" height="50" viewBox="0 0 1200 50"><polygon points="0,0 1200,0 1200,2 0,48" fill="#f2f2f2"/></svg>
<h2 class="section-title abs" style="left:0;top:2468px;width:1200px;text-align:center;color:#fff">Recipes</h2>
<div class="recipe-card" style="left:76px;background:linear-gradient(135deg,#6a3b1c,#b7763a 55%,#3a2213)" role="img" aria-label="Roast turkey with vegetables"></div>
<div class="recipe-card" style="left:340px;background:linear-gradient(135deg,#b0281a,#e04a2a 50%,#4a1a12)" role="img" aria-label="Red lobsters and crabs with lemon"></div>
<div class="recipe-card" style="left:607px;background:linear-gradient(135deg,#3a2a22,#8a5a3e 50%,#2a1e18)" role="img" aria-label="Grilled steak on a wooden board"></div>
<div class="recipe-card" style="left:873px;background:linear-gradient(135deg,#8a2a12,#c2642a 45%,#3b5a1e)" role="img" aria-label="Grilled chicken with herbs and tomatoes"></div>
<svg class="abs" style="left:44px;top:2614px" width="16" height="28" viewBox="0 0 16 28"><polyline points="14,2 2,14 14,26" fill="none" stroke="#fff" stroke-width="2.5"/></svg>
<svg class="abs" style="left:1138px;top:2614px" width="16" height="28" viewBox="0 0 16 28"><polyline points="2,2 14,14 2,26" fill="none" stroke="#fff" stroke-width="2.5"/></svg>
<div class="btn-light" style="left:425px;width:164px">View Menu</div>
<div class="btn-light" style="left:611px;width:166px">View Recipes</div>

<!-- Testimonials -->
<h2 class="section-title abs" style="left:76px;top:2918px">Testimonials</h2>
<div class="abs" style="left:76px;top:2973px;width:148px;height:148px;border-radius:50%;background:radial-gradient(circle at 50% 40%,#d8c7b4,#9a8774 60%,#5b4d42)" role="img" aria-label="Portrait of a smiling client"></div>
<svg class="abs" style="left:188px;top:3018px" width="52" height="52" viewBox="0 0 52 52">
  <circle cx="26" cy="26" r="24" fill="#3d3129" stroke="#fff" stroke-width="3"/>
  <path d="M15 31 q0-10 8-13 v3 q-4 2-4 5 h4 v7 h-8z M28 31 q0-10 8-13 v3 q-4 2-4 5 h4 v7 h-8z" fill="#fff"/>
</svg>
<p class="quote-text">Aliquam molestie, mi et imperdiet euismod, dui purus auctor tellus, et interdum lacus lectus et ante. Sed accumsan sollicitudin sapien, sit amet adipiscing turpis gravida ac. In congue, neque ac lobortis volutpat, libero mauris varius mi..</p>
<p class="abs" style="left:257px;top:3094px;font-size:16px;font-weight:700;color:var(--green)">-Name Heading</p>

<!-- Join email -->
<h2 class="section-title abs" style="left:795px;top:2918px">Join Email</h2>
<p class="abs" style="left:795px;top:2968px;width:340px;font-size:15px;line-height:28px">Aliquam molestie, mi et imperdiet euismod, dui purus auctor tellus..</p>
<div class="email-field">Enter Email Address</div>
<div class="btn-outline" style="left:1014px;top:3085px;width:112px;height:40px;font-size:14px">Sign Up</div>

<!-- Footer -->
<svg class="abs" style="left:0;top:3155px" width="1200" height="203" viewBox="0 0 1200 203">
  <polygon points="0,0 1200,0 1200,203 0,203" fill="#161616"/>
  <polygon points="0,0 500,0 440,34 60,34 0,10" fill="#fff"/>
</svg>
<nav class="footer-nav"><span>Home</span><span>About Chef</span><span>Menu</span><span>Recipes</span><span>How It Works</span><span>Services</span><span>Get In Touch</span></nav>
<div class="footer-brand">Leo Chef</div>
<p class="footer-copy">Copyright © 2016<br>All Right Reserved &nbsp;| &nbsp;Terms of Services</p>
<div class="social"><span></span><span></span><span></span><span></span><span></span><span></span></div>

</body>
</html>
```